www.marvenholt.com

Updating website so looks futristic but yet business like and easy to navigate, essentially a good landing page with a cool picture summing up what we do, and links to the following pages, all other pages on site to be updated, Exclusive Distributor of Brisk Forge Unique Fitness Equipment Products in UK & Ireland, www.crestvolley.co.uk Exclusive Partners & Distributors Of Crest Volley - Obstacle Races - Obstacle Hire - Obstacle Training - Adventure Events, www.goplumwick.co.uk Adventures That Inspire. We also Health Club / Facillity Consultancy

```html
<!DOCTYPE html>
<html lang="en">
<head>
<meta charset="utf-8">
<title>Marven Holt – Health &amp; Wellness</title>
<link href="https://fonts.googleapis.com/css2?family=Open+Sans:wght@400;700&family=Oswald:wght@500&family=Abel&display=swap" rel="stylesheet">
<style>
:root{
  --bg:#050505;
  --bg-pattern:#1a1a1a;
  --card:#2b2b2b;
  --text:#ffffff;
  --accent:#e8650f;
  --muted:#9a9a9a;
  --media:#3a3a3a;
}
*{margin:0;padding:0;box-sizing:border-box}
html,body{width:960px;height:1200px;overflow:hidden;background:var(--bg)}
.page{position:relative;width:960px;height:1200px;overflow:hidden;
  background:radial-gradient(ellipse at 50% 60%,#161616 0%,#0a0a0a 55%,var(--bg) 100%);
  color:var(--text);font-family:"Open Sans",sans-serif}
.testimonial{position:absolute;left:143px;width:678px;background:var(--card);padding:0 16px}
.testimonial p{font-size:8.6px;line-height:10.4px;margin-bottom:8px}
.testimonial .signature{font-weight:700;font-size:8.6px;margin-top:14px}
.logo-badge{position:absolute;left:447px;width:74px;height:74px;border-radius:50%;
  background:#fff;border:3px solid #cfcfcf;display:flex;align-items:center;justify-content:center;
  font-size:9px;font-weight:700;color:#333;text-align:center;line-height:10px}
.divider{position:absolute;left:192px;width:576px;height:2px;
  background:linear-gradient(90deg,transparent,var(--accent) 25%,var(--accent) 75%,transparent)}
.section-title{position:absolute;left:0;width:960px;text-align:center;font-family:"Oswald",sans-serif;
  font-weight:500;font-size:29px;letter-spacing:.5px;line-height:34px}
.section-title span{display:inline-block;padding:0 10px 4px;border-bottom:2px solid var(--text)}
.section-lead{position:absolute;left:160px;width:640px;text-align:center;font-family:"Abel",sans-serif;
  font-size:13px;line-height:16px}
.section-lead .brand{color:var(--accent)}
.video{position:absolute;left:60px;width:488px;background:#000;overflow:hidden}
.video .frame{position:absolute;top:0;bottom:0;left:35px;right:36px}
.video .title{position:absolute;left:8px;top:6px;font-size:9.5px;font-family:Arial,sans-serif}
.video .title.lg{font-size:11.5px;left:12px;top:8px}
.video .more{position:absolute;left:10px;bottom:36px;font-size:5.5px;font-family:Arial,sans-serif}
.video .bar{position:absolute;left:6px;right:8px;bottom:20px;height:2px;background:#555}
.video .bar i{display:block;width:17%;height:100%;background:#e02020}
.video .time{position:absolute;left:52px;bottom:7px;font-size:6px;font-family:Arial,sans-serif}
.video .player-name{position:absolute;right:26px;bottom:6px;font-size:8px;font-family:"Abel",sans-serif}
.video svg.icons{position:absolute;left:0;top:0}
.photo{position:absolute}
</style>
</head>
<body>
<div class="page">

  <article class="testimonial" style="top:0;height:163px;padding-top:38px">
    <p>Brookfell Community Leisure commissioned Marven Holt in January 2015 to provide sales training to a new group of Sales Consultants that had been employed for a period of 3 months to boost the sales during the busiest period of the year. The training ran over two days and was both informative and practical using information from the industry to back up the processes and procedures that were to be introduced by the new team. Simple easy to understand exercises meant that all that attended the training fully understood their roles and responsibilities by the end and the consequences of not following the systems. The result from this training was that we had a sales team that were able to hit the ground running and also achieved the best ever January figures we have had, back up with a great marketing campaign to drive prospects into the building. Working with Rory was professional, informative enjoyable and hopefully we will build on this success and use Marven Holt in the future.</p>
    <p class="signature">Dana Corrow - Executive Regional Manager - Brookfell Community Leisure</p>
  </article>
  <div class="logo-badge" style="top:-50px"></div>

  <article class="testimonial" style="top:220px;height:149px;padding-top:54px">
    <p>Tidewell Fitness have utilised the in depth, health, wellness and fitness industry knowledge and expertise that Rory and the team have. The Marven Holt Team have provided excellent profitable sales for us very quickly and continue to do so under our rapid expansion plans.</p>
    <p>The knowledge that Marven Holt bring to the table is without doubt priceless for our business. We will continue to collaborate with Rory and the Marven Holt team in 2016 as we grow from strength to strength in the market place. I whole heartedly recommend Rory &amp; Marven Holt</p>
    <p class="signature" style="margin-top:12px">Owen Pardee - General Manager - Tidewell Fitness UK</p>
  </article>
  <div class="logo-badge" style="top:183px">Tidewell<br>Fitness</div>

  <!-- Health -->
  <div class="divider" style="top:449px"></div>
  <h2 class="section-title" style="top:482px"><span>HEALTH</span></h2>
  <p class="section-lead" style="top:532px"><span class="brand">Marven Holt</span> long term success depends on the talents commitment and shared values of our people, Marven Holt is made of a unique hand picked team that will ensure the best possible service is delivered,</p>

  <div class="video" style="top:612px;height:234px">
    <div class="frame" role="img" aria-label="Children running at the start of a kids obstacle race" style="background:linear-gradient(180deg,#5a6a80 0%,#7b7068 50%,#a08a70 100%)"></div>
    <div class="title">Summit Kids Dash</div>
    <div class="more">MORE VIDEOS</div>
    <div class="bar"><i></i></div>
    <div class="time">0:18 / 1:46</div>
    <div class="player-name">Clipstream</div>
    <svg class="icons" width="488" height="234" viewBox="0 0 488 234">
      <circle cx="432" cy="12" r="4.5" fill="none" stroke="#fff" stroke-width="1.3"/>
      <path d="M448 15 l8-5 l-8-5 v3 h-4 v4 h4z" fill="#fff"/>
      <circle cx="471" cy="12" r="5" fill="#fff"/><rect x="470.3" y="10.5" width="1.4" height="4" fill="#000"/>
      <path d="M14 208 v10 l8-5z" fill="#fff"/>
      <path d="M35 210 h3 l4-3 v12 l-4-3 h-3z" fill="#fff"/>
      <rect x="393" y="210" width="9" height="7" fill="none" stroke="#fff" stroke-width="1.2"/>
      <circle cx="416" cy="213.5" r="3.5" fill="#fff"/>
      <path d="M468 209 h-3 v3 M474 209 h3 v3 M468 218 h-3 v-3 M474 218 h3 v-3" stroke="#fff" fill="none" stroke-width="1.2"/>
    </svg>
  </div>

  <div class="photo" role="img" aria-label="Team crossing a muddy obstacle course" style="left:594px;top:614px;width:109px;height:70px;background:linear-gradient(160deg,#7d8070,#4a4038)"></div>
  <div class="photo" role="img" aria-label="Athlete on a beach obstacle at sunset" style="left:594px;top:688px;width:109px;height:60px;background:linear-gradient(180deg,#c9b89a,#6a5a48)"></div>
  <div class="photo" role="img" aria-label="Trainer beside a climbing frame in a field" style="left:706px;top:614px;width:134px;height:133px;background:linear-gradient(180deg,#8fb0d8 0%,#b8c8d8 45%,#4f6a3a 100%)"></div>

  <!-- Wellness -->
  <div class="divider" style="top:903px"></div>
  <h2 class="section-title" style="top:927px"><span>WELLNESS</span></h2>
  <p class="section-lead" style="top:978px"><span class="brand">Marven Holt</span> long term success depends on the talents commitment and shared values of our people, Marven Holt is made of a unique hand picked team that will ensure the best possible service is delivered,</p>

  <div class="video" style="top:1058px;height:142px">
    <div class="frame" role="img" aria-label="Wellness technology programme video still" style="left:0;right:0;background:linear-gradient(135deg,#8a8a8a 0%,#5a5a5a 50%,#2a2a2a 100%)"></div>
    <div class="title lg">Vitaloop Technology Programme</div>
    <svg class="icons" width="488" height="142" viewBox="0 0 488 142">
      <circle cx="441" cy="14" r="6.5" fill="#fff"/><path d="M441 10 v4 h3" stroke="#555" stroke-width="1.3" fill="none"/>
      <path d="M463 18 l10-6 l-10-6 v3 h-5 v6 h5z" fill="#fff"/>
      <rect x="221" y="108" width="48" height="24" rx="6" fill="#222" opacity=".8"/>
      <path d="M240 114 v12 l10-6z" fill="#fff"/>
    </svg>
  </div>

  <div class="photo" role="img" aria-label="Black and white city skyline from above" style="left:592px;top:1058px;width:288px;height:110px;background:linear-gradient(180deg,#d8d8d8 0%,#8a8a8a 40%,#3a3a3a 100%)"></div>
  <div class="photo" role="img" aria-label="Printed page of text" style="left:598px;top:1175px;width:134px;height:25px;background:#e4e2dc"></div>
  <div class="photo" role="img" aria-label="Speaker presenting on stage" style="left:738px;top:1175px;width:142px;height:25px;background:linear-gradient(90deg,#4a7aa8,#9ab8d0)"></div>

</div>
</body>
</html>
```